Quillmarsh Property Solutions need a business card design

Hello guys. We would need a business card design asap please.
We are a start up property investment business based in London UK specialised in buying, selling, managing and letting properties and helping distressed property owners.
The name of our Business is Quillmarsh, the logo symbolises the four fundamental elements of the world (earth, air, fire and water) and so it stands for strength, stability, longevity.
We would like the business card to communicate professionalism and reliability. Many many thanks indeed for your work.

Details:

1.) Rosalind Updike
Property Investor
Mobile: +44(0)7700123456
Email: rosalind.quillmarsh@mailbox-example.com

2.) Dominic Updike
Property Investor
Mobile: +44(0)7700987654
Email: dominic.quillmarsh@mailbox-example.com

```html
<!DOCTYPE html>
<html lang="en">
<head>
<meta charset="utf-8">
<title>Quillmarsh Property Solutions – Business Card</title>
<link rel="stylesheet" href="https://fonts.googleapis.com/css2?family=Ubuntu:wght@400;500;700&display=swap">
<style>
  :root {
    --page-bg: #e9e7e3;
    --card-white: #ffffff;
    --panel-blue: #2f63c9;
    --divider-red: #d4252f;
    --ink: #111111;
    --on-dark: #ffffff;
    --green-light: #2bb04f;
    --green-deep: #1c9a3c;
    --shadow: rgba(0, 0, 0, 0.18);
  }

  * { box-sizing: border-box; margin: 0; padding: 0; }

  html, body {
    width: 1200px;
    height: 720px;
    overflow: hidden;
  }

  body {
    background: var(--page-bg);
    font-family: "Ubuntu", sans-serif;
    display: flex;
    align-items: center;
    justify-content: center;
    gap: 40px;
  }

  .card {
    width: 540px;
    height: 310px;
    position: relative;
    overflow: hidden;
    box-shadow: 0 6px 18px var(--shadow);
  }

  /* Front side */
  .card-front {
    display: flex;
    background: var(--card-white);
  }

  .brand-side {
    width: 236px;
    display: flex;
    align-items: center;
    justify-content: center;
    gap: 10px;
    padding: 0 18px;
  }

  .brand-mark {
    width: 16px;
    height: 16px;
    flex: none;
    background: var(--divider-red);
  }

  .brand-name {
    font-weight: 700;
    font-size: 17px;
    line-height: 1.2;
    color: var(--ink);
    text-transform: uppercase;
    letter-spacing: 0.02em;
  }

  .divider {
    width: 14px;
    flex: none;
    background: var(--card-white);
    position: relative;
  }

  .divider::after {
    content: "";
    position: absolute;
    top: 0;
    bottom: 0;
    left: 4px;
    width: 3px;
    background: var(--divider-red);
  }

  .contact-side {
    flex: 1;
    background: var(--panel-blue);
    color: var(--on-dark);
    padding: 52px 18px 0 22px;
  }

  .person-name {
    font-weight: 700;
    font-size: 19px;
    margin-bottom: 6px;
  }

  .person-role {
    font-size: 13px;
    margin-bottom: 10px;
  }

  .contact-line {
    display: flex;
    align-items: center;
    gap: 7px;
    font-size: 11.5px;
    margin-bottom: 6px;
    white-space: nowrap;
  }

  .contact-icon {
    width: 12px;
    height: 12px;
    flex: none;
  }

  /* Back side */
  .card-back {
    background: radial-gradient(circle at 50% 40%, var(--green-light), var(--green-deep) 75%);
    color: var(--on-dark);
    display: flex;
    flex-direction: column;
    align-items: center;
    justify-content: center;
    gap: 26px;
  }

  .back-brand {
    display: flex;
    align-items: center;
    gap: 14px;
  }

  .back-brand .brand-mark {
    width: 26px;
    height: 26px;
  }

  .back-brand .brand-name {
    color: var(--on-dark);
    font-size: 30px;
    text-align: left;
  }

  .website {
    font-size: 17px;
    letter-spacing: 0.08em;
    font-weight: 500;
  }
</style>
</head>
<body>

  <section class="card card-front" aria-label="Business card, front">
    <div class="brand-side">
      <span class="brand-mark"></span>
      <span class="brand-name">Quillmarsh<br>Property Solutions</span>
    </div>
    <div class="divider"></div>
    <div class="contact-side">
      <p class="person-name">Rosalind Updike</p>
      <p class="person-role">Property Investor</p>
      <p class="contact-line">
        <svg class="contact-icon" viewBox="0 0 12 12" aria-hidden="true">
          <rect x="3" y="0.5" width="6" height="11" rx="1.2" fill="none" stroke="#fff" stroke-width="1.2"/>
          <circle cx="6" cy="9.5" r="0.8" fill="#fff"/>
        </svg>
        +44(0)7700123456
      </p>
      <p class="contact-line">
        <svg class="contact-icon" viewBox="0 0 12 12" aria-hidden="true">
          <rect x="0.8" y="2.5" width="10.4" height="7.5" rx="1" fill="none" stroke="#fff" stroke-width="1.2"/>
          <path d="M1 3 L6 7 L11 3" fill="none" stroke="#fff" stroke-width="1.2"/>
        </svg>
        rosalind.quillmarsh@mailbox-example.com
      </p>
    </div>
  </section>

  <section class="card card-back" aria-label="Business card, back">
    <div class="back-brand">
      <span class="brand-mark"></span>
      <span class="brand-name">Quillmarsh</span>
    </div>
    <p class="website">www.quillmarsh-example.com</p>
  </section>

</body>
</html>
```